Brel Fosk Painting, Eco and Non toxic painting client information brochure.

Brel fosk painting is a painting company that specialises in eco and non toxic paints. This brochure will be left with the client after the initial meeting to explain about my business and hopefully win the job. By reading the text i have provided (see attachment) you can get a better understanding of what we do.
The brochure should be fresh and clean looking, complimenting the Brel Fosk Painting logo and the text provided.
This will be printed onto a recycled paper.
Text and font must clear and easy to read.

Please have a look at my web page. I will be redoing this soon as well but this will give you some ideas of where I'm at.

Would like some picture but not sure what.
I have attached some pics but they don't have to be use
Updates

Hi peeps,

Thanks for all the great designs and sorry i haven't got back to you sooner.
been a bit busy.
Tomorrow i hope to be able to sit down and have a good look at what everybody has done.
Thanks again i really appreciate the effort.

kind regards oswin 

hi designers,

Just sat down and had a good look at the designs sent in and there are some crackers.
Its going to be very difficult to choose. I have only 1 day left before it closes so ill wait till then to see if there are any more submissions come in then ill get back to everybody.
Thanks again for your time and effort.

kind regards oswin 

Hi too all you designers that have worked on my project. 

I am always amazed at all the different designs that come through. Super work guys and girls. 
I have narrowed it down to a couple of designs.
Ill be making the decision tonight.
Thanks again to you all and i really appreciate all the hard work.
I will be doing another brochure in the future for more architecture / builder focus and there were a few designs that would work perfectly for this.

Kinds regards oswin  

Target Market(s)

The work we do is mainly residential repaints, family homes
Mostly I am dealing with the wife of the family or female designers/architects

Industry/Entity Type

Painting

Requirements
Must have
• Company logo, either white or black version what ever suits best.
Text that has been provided.
Brochure will be 1 page A 4, folded into 3 parts both sides.
Front page must have logo and
SPECIALSING IN:
NON TOXIC
ECO FRIENDLY &
HEAT REFLECTIVE PAINTS
Phone 041 382 6190
Painting@brelfosk.biz
www.brelfosk.biz

```html
<!DOCTYPE html>
<html lang="en">
<head>
<meta charset="utf-8">
<title>Brel Fosk Painting – Client Brochure</title>
<link href="https://fonts.googleapis.com/css2?family=Open+Sans:wght@400;600;700&display=swap" rel="stylesheet">
<style>
  :root {
    --page-bg: #efe6d3;
    --green: #4f9a2c;
    --green-dark: #3c7d1f;
    --green-light: #9fd35a;
    --white: #ffffff;
    --ink: #2b2b2b;
    --photo-top: #cfd1cf;
    --photo-top-2: #9ea3a2;
    --photo-bottom: #d9d6cc;
    --photo-bottom-2: #b9a24a;
  }
  * { box-sizing: border-box; margin: 0; padding: 0; }
  html, body {
    width: 1200px; height: 872px; overflow: hidden;
    background: var(--page-bg);
    font-family: "Open Sans", Arial, sans-serif;
  }
  .brochure {
    position: absolute; left: 60px; top: 54px;
    width: 1080px; height: 764px;
    box-shadow: 0 10px 30px rgba(0,0,0,.18);
  }
  .brochure__art { position: absolute; inset: 0; }
  .panel-text {
    position: absolute; color: var(--white);
    font-size: 13px; line-height: 1.5;
  }
  .panel-text p + p { margin-top: 10px; }
  .panel-text__title { font-weight: 700; text-transform: uppercase; }
  .panel-text--vocs { left: 36px; top: 306px; width: 300px; }
  .panel-text--about { left: 396px; top: 320px; width: 292px; }
  .phone-inside {
    position: absolute; left: 480px; top: 632px; width: 220px;
    text-align: right; color: var(--white);
    font-weight: 700; font-size: 19px; letter-spacing: .5px;
  }
  .cover {
    position: absolute; left: 720px; top: 0; width: 360px; height: 764px;
    color: var(--white); text-align: center;
  }
  .logo {
    position: absolute; left: 80px; top: 292px; width: 200px; height: 52px;
    background: var(--white); border-radius: 12px;
    display: flex; align-items: center; justify-content: center; gap: 8px;
    box-shadow: 0 2px 4px rgba(0,0,0,.2);
  }
  .logo__mark { width: 12px; height: 12px; background: var(--green); }
  .logo__name {
    color: var(--ink); font-weight: 700; font-size: 14px;
    text-transform: uppercase; letter-spacing: .3px;
  }
  .specialities {
    position: absolute; left: 0; top: 372px; width: 360px;
    font-weight: 600; font-size: 15px; line-height: 1.75;
  }
  .cover__rule {
    position: absolute; left: 110px; top: 484px; width: 140px;
    border-top: 1px solid rgba(255,255,255,.7);
  }
  .cover__phone {
    position: absolute; left: 0; top: 500px; width: 360px;
    font-weight: 700; font-size: 22px; letter-spacing: .5px;
  }
  .cover__contacts {
    position: absolute; left: 20px; top: 708px; width: 320px;
    display: flex; justify-content: space-between;
    font-size: 11px; font-weight: 600;
  }
</style>
</head>
<body>
<main class="brochure">
  <svg class="brochure__art" viewBox="0 0 1080 764" width="1080" height="764">
    <defs>
      <linearGradient id="photoTop" x1="0" y1="0" x2="1" y2="1">
        <stop offset="0" stop-color="var(--photo-top)"/>
        <stop offset="1" stop-color="var(--photo-top-2)"/>
      </linearGradient>
      <linearGradient id="photoBottom" x1="0" y1="0" x2="1" y2="0">
        <stop offset="0" stop-color="var(--photo-bottom)"/>
        <stop offset=".5" stop-color="var(--photo-bottom-2)"/>
        <stop offset="1" stop-color="var(--photo-bottom)"/>
      </linearGradient>
      <linearGradient id="greenBody" x1="0" y1="0" x2="1" y2="1">
        <stop offset="0" stop-color="var(--green-dark)"/>
        <stop offset=".5" stop-color="var(--green)"/>
        <stop offset="1" stop-color="var(--green-dark)"/>
      </linearGradient>
    </defs>
    <rect class="green-body" width="1080" height="764" fill="url(#greenBody)"/>
    <path role="img" aria-label="Photo of a bright modern living room with white sofas and shelving"
          d="M0 0 H720 V246 C620 240 520 282 360 282 C240 282 120 250 0 220 Z" fill="url(#photoTop)"/>
    <path class="wave-line" d="M0 220 C120 250 240 282 360 282 C520 282 620 240 720 246"
          fill="none" stroke="var(--green-light)" stroke-width="6"/>
    <path role="img" aria-label="Photo of a modern lounge with a red coffee table and woven armchair"
          d="M720 0 H1080 V150 C1040 230 960 258 720 246 Z" fill="url(#photoTop)"/>
    <path class="wave-line" d="M720 246 C960 258 1040 230 1080 150"
          fill="none" stroke="var(--green-light)" stroke-width="6"/>
    <path role="img" aria-label="Photo of a lounge with yellow sofas and warm downlights"
          d="M0 652 C160 620 320 622 440 640 C580 662 660 690 720 742 V764 H0 Z" fill="url(#photoBottom)"/>
    <path class="wave-line" d="M0 652 C160 620 320 622 440 640 C580 662 660 690 720 742"
          fill="none" stroke="var(--green-light)" stroke-width="6"/>
    <path class="cover-band" d="M720 690 H1080 V740 H720 Z" fill="var(--green-dark)" opacity=".8"/>
    <line class="fold" x1="360" y1="0" x2="360" y2="764" stroke="rgba(0,0,0,.08)"/>
    <line class="fold" x1="720" y1="0" x2="720" y2="764" stroke="rgba(0,0,0,.08)"/>
  </svg>

  <section class="panel-text panel-text--vocs">
    <p><span class="panel-text__title">VOCs = Volatile Organic Compounds</span><br>
    VOCs are hazardous chemicals that are emitted from paints. This occurs even after the paint has dried, paints can continue too emit VOCs for several years after application.</p>
    <p>By using low VOC emitting paints, fewer chemicals are released than traditional paints. In choosing a zero VOC option, you will experience no odour after the paint has dried and will be helping improve air quality both inside and outside your home or business.</p>
  </section>

  <section class="panel-text panel-text--about">
    <p>At Brel Fosk Painting we choose to use these products and a green business approach because we care about our clients, workers and the overall environment.</p>
    <p>We can help make a difference, not just by changing the colour of your home or business but by giving you a better, safer environment in which to live and work.</p>
  </section>

  <div class="phone-inside">041 382 6190</div>

  <section class="cover">
    <div class="logo">
      <span class="logo__mark"></span>
      <span class="logo__name">Brel Fosk Painting</span>
    </div>
    <p class="specialities">Specialising in:<br>Non Toxic<br>Eco Friendly &amp;<br>Heat Reflective Paints</p>
    <div class="cover__rule"></div>
    <p class="cover__phone">041 382 6190</p>
    <div class="cover__contacts">
      <span>Painting@brelfosk.biz</span>
      <span>www.brelfosk.biz</span>
    </div>
  </section>
</main>
</body>
</html>
```